Design my dad a new business card because his current one sucks!

I need a business card designed for my fathers home maintenance business. His customers are individuals (single moms, old people etc.) as well as the occasional business. As such it needs to be accessible to both target audiences.

The front of the card should be dark grey on yellow with the logo and contain the following information:
- Darren Holtwick
- 0488 274 915
- info@brightoakhomecare.com.au
- 0488 274 915

- ABN: 71 284 630 912
- 'Fully Insured'

The reverse should be yellow on dark grey and will have the web address:
- brightoakhomecare.com.au

And a few key services he offers:
GENERAL REPAIRS
PAINTING/TILING/
PAVING &CONCRETING
PRESSURE WASHING
ON-SITE WELDING
DECKING ADDITIONS & REPAIRS
FENCING
FULL BOND CLEANING

This will be first time the logo has been printed so you will need to come up with the best CMYK approximation of the RGB colours to make sure it is a close as possible.

```html
<!DOCTYPE html>
<html lang="en">
<head>
<meta charset="utf-8">
<title>Bright Oak Home Care – Business Card</title>
<link rel="stylesheet" href="https://fonts.googleapis.com/css2?family=Open+Sans:wght@400;700&display=swap">
<style>
  :root {
    --yellow-core: #fff200;
    --yellow-mid: #fde400;
    --yellow-edge: #f6c500;
    --ink-dark: #1c1c1c;
    --ink-grey: #5a5a5c;
  }
  * { margin: 0; padding: 0; box-sizing: border-box; }
  html, body {
    width: 1200px;
    height: 686px;
    overflow: hidden;
    background: var(--yellow-edge);
  }
  .card {
    position: relative;
    width: 1200px;
    height: 686px;
    overflow: hidden;
    font-family: "Open Sans", Arial, sans-serif;
    color: var(--ink-grey);
    background: radial-gradient(ellipse 620px 420px at 600px 300px,
      var(--yellow-core) 0%, var(--yellow-mid) 45%, var(--yellow-edge) 100%);
  }
  .brand-name {
    position: absolute;
    left: 265px;
    top: 250px;
    width: 725px;
    text-align: center;
    font-size: 70px;
    font-weight: 700;
    line-height: 1;
    letter-spacing: -1px;
    color: var(--ink-dark);
    white-space: nowrap;
  }
  .insured {
    position: absolute;
    left: 736px;
    top: 415px;
    font-size: 27px;
    font-weight: 400;
    line-height: 1.2;
    color: var(--ink-grey);
  }
  .holder-name {
    position: absolute;
    left: 31px;
    top: 430px;
    font-size: 45px;
    font-weight: 700;
    line-height: 1.2;
    color: var(--ink-grey);
  }
  .contact-row {
    position: absolute;
    left: 180px;
    display: flex;
    align-items: center;
  }
  .contact-row.phone { top: 520px; }
  .contact-row.email { top: 598px; }
  .contact-icon {
    width: 64px;
    flex: none;
    margin-right: 58px;
  }
  .contact-text {
    font-size: 35px;
    font-weight: 400;
    line-height: 1.2;
    color: var(--ink-grey);
    white-space: nowrap;
  }
  .abn {
    position: absolute;
    right: 18px;
    top: 642px;
    font-size: 26px;
    font-weight: 400;
    line-height: 1.2;
    color: var(--ink-grey);
  }
</style>
</head>
<body>
<main class="card">
  <div class="brand-name">Bright Oak Home Care</div>
  <p class="insured">Fully Insured</p>

  <h1 class="holder-name">Darren Holtwick</h1>

  <div class="contact-row phone">
    <svg class="contact-icon" viewBox="0 0 64 54" aria-hidden="true" fill="none" stroke="#5a5a5c" stroke-width="3" stroke-linejoin="round">
      <path d="M4 18 C4 6 60 6 60 18 L60 22 L46 22 L46 16 L18 16 L18 22 L4 22 Z"/>
      <path d="M12 26 L20 22 L44 22 L52 26 L54 50 L10 50 Z"/>
      <circle cx="32" cy="36" r="7"/>
    </svg>
    <span class="contact-text">0488 274 915</span>
  </div>

  <div class="contact-row email">
    <svg class="contact-icon" viewBox="0 0 64 38" aria-hidden="true" fill="none" stroke="#5a5a5c" stroke-width="3" stroke-linejoin="round">
      <rect x="3" y="3" width="58" height="32" rx="2"/>
      <path d="M3 3 L32 24 L61 3"/>
      <path d="M3 35 L24 18 M61 35 L40 18"/>
    </svg>
    <span class="contact-text">info@brightoakhomecare.com.au</span>
  </div>

  <p class="abn">ABN: 71 284 630 912</p>
</main>
</body>
</html>
```